Briloran Clear Springs needs a new business card design (we produce and sell pure bottled water)

We need a clean modern design for our new business cards, We have an existing logo which ultimately cannot be changed, however it could be slighty improved and the colours adjusted. We have this existing logo on all of our bottles, vehicles etc.

Our company slogan is "Pure down to the last drop".
Along with our relevant company information
(Address, phone, website email etc) we will only be using names and not putting position titles for flexibilty.

We are looking for a clean, minimalist modern design.

You can view our website (if need of an update also!) to see our business.

Industry/Entity Type

Business

Contact Information for Business Card

Staff Name : XXXXXX XXXXXX
Address : 9/41 Tavenor St
Halden Rise QLD 4172
Staff Mobile Number : 04XX XXX XXX
Office Phone Number : 07 3918 2457
Staff Email Address : XXXX@brilorancleargo.com.au
Website : www.brilorancleargo.com.au

Font styles to use
Sans Serif

Colors
cee9f5
33a6d7
0492cd
0455a3
3276b5
85abd2
cedeed

Requirements
Must have
• The ability to edit and change the staff members details as we will need to edit for each respective staff member (7 in total)

```html
<!DOCTYPE html>
<html lang="en">
<head>
<meta charset="utf-8">
<title>Briloran Clear Springs – Business Card</title>
<link rel="stylesheet" href="https://fonts.googleapis.com/css2?family=Open+Sans:wght@400;700;800&display=swap">
<style>
  :root {
    --bg: #e6e7ea;
    --card: #ffffff;
    --brand-blue: #0455a3;
    --brand-mid: #3276b5;
    --text-dark: #1d1d24;
    --band-text: #ffffff;
    --shadow: rgba(0, 0, 0, 0.18);
  }
  * { box-sizing: border-box; margin: 0; padding: 0; }
  html, body {
    width: 1200px;
    height: 1200px;
    overflow: hidden;
    background: var(--bg);
    font-family: "Open Sans", Arial, sans-serif;
  }
  .canvas {
    position: relative;
    width: 1200px;
    height: 1200px;
  }
  .business-card {
    position: absolute;
    left: 75px;
    top: 300px;
    width: 1050px;
    height: 600px;
    background: var(--card);
    box-shadow: 0 14px 40px var(--shadow);
    overflow: hidden;
  }
  .brand-block {
    position: absolute;
    left: 50px;
    top: 250px;
    width: 370px;
    display: flex;
    align-items: center;
    gap: 18px;
  }
  .brand-mark {
    flex: 0 0 auto;
    width: 46px;
    height: 46px;
    border-radius: 50%;
    background: var(--brand-blue);
  }
  .brand-name {
    color: var(--brand-blue);
    font-weight: 800;
    font-size: 44px;
    line-height: 1.02;
    text-transform: uppercase;
    letter-spacing: 0.5px;
  }
  .divider {
    position: absolute;
    left: 455px;
    top: 20px;
    width: 2px;
    height: 420px;
    background: var(--brand-blue);
  }
  .staff-name {
    position: absolute;
    left: 500px;
    top: 60px;
    color: var(--brand-blue);
    font-size: 42px;
    font-weight: 400;
  }
  .contact-list {
    position: absolute;
    left: 500px;
    top: 285px;
    list-style: none;
  }
  .contact-item {
    display: flex;
    align-items: center;
    gap: 16px;
    color: var(--text-dark);
    font-size: 30px;
    line-height: 48px;
    white-space: nowrap;
  }
  .contact-icon {
    width: 26px;
    height: 26px;
    flex: 0 0 auto;
  }
  .address-band {
    position: absolute;
    left: 0;
    bottom: 0;
    width: 100%;
    height: 120px;
    background: var(--brand-blue);
    display: flex;
    align-items: center;
    padding-left: 470px;
    color: var(--band-text);
    font-size: 30px;
    font-weight: 400;
    white-space: nowrap;
  }
</style>
</head>
<body>
<main class="canvas">
  <section class="business-card" aria-label="Business card front">
    <div class="brand-block">
      <span class="brand-mark" aria-hidden="true"></span>
      <span class="brand-name">Briloran<br>Clear Springs</span>
    </div>

    <div class="divider" aria-hidden="true"></div>

    <h1 class="staff-name">Marla Quenby</h1>

    <ul class="contact-list">
      <li class="contact-item">
        <svg class="contact-icon" viewBox="0 0 26 26" aria-hidden="true">
          <rect width="26" height="26" rx="3" fill="#0455a3"/>
          <path d="M8 6c1 0 2 2.5 2 3s-1.2 1.2-1 2c.6 2 2.2 3.6 4.2 4.2.8.2 1.5-1 2-1s3 1 3 2c0 1.5-1.5 2.8-3 2.6C10 18 7.8 15.8 6.2 10.6 5.8 8 6.8 6 8 6z" fill="#ffffff"/>
        </svg>
        <span>07 3918 2457</span>
      </li>
      <li class="contact-item">
        <svg class="contact-icon" viewBox="0 0 26 26" aria-hidden="true">
          <rect width="26" height="26" rx="3" fill="#0455a3"/>
          <rect x="5.5" y="8" width="15" height="10.5" fill="none" stroke="#ffffff" stroke-width="1.8"/>
          <path d="M5.5 8l7.5 6 7.5-6" fill="none" stroke="#ffffff" stroke-width="1.8"/>
        </svg>
        <span>XXXX@brilorancleargo.com.au</span>
      </li>
      <li class="contact-item">
        <svg class="contact-icon" viewBox="0 0 26 26" aria-hidden="true">
          <rect width="26" height="26" rx="3" fill="#0455a3"/>
          <circle cx="13" cy="13" r="7" fill="none" stroke="#ffffff" stroke-width="1.8"/>
          <path d="M6 13h14M13 6c-3 3.5-3 10.5 0 14M13 6c3 3.5 3 10.5 0 14" fill="none" stroke="#ffffff" stroke-width="1.4"/>
        </svg>
        <span>www.brilorancleargo.com.au</span>
      </li>
    </ul>

    <footer class="address-band">9/41 Tavenor St Halden Rise QLD 4172</footer>
  </section>
</main>
</body>
</html>
```